Corporate brochure design 4 pages

Hi,

We are a real estate company based in Europe.

We have almost finalized a rebranding.

We are developing a brand book guidelines (still on working process) to help you undertstand the look and feel of our new CI. I would like to receive proposals of design for a corporate brochure template. I need to receive the Indesign files with full ownership rights to be able to adapt all our documentation with this template.
Regarding the images, you can take gabaris on www.pelvarimages.example. I will be able to take them afterwards.

There will be 4 pages. you will receive the 4 pages on pdf for your consideration with our (almost) actual layout.

- 1st page: cover
- 2nd page: company presentation in french and english
- 3rd page: some market data + graph
- 4th page: 2 retail centers presentation.

In the template, i need to have:
- the paragraph styles in order
- 2 different masters with top/bottom/page number aso.

Please feel free to ask any other questions.

best regards,
Updates

I would like to precise tha t we are active on the commercial real estate sector:

- office transactions (rent /sales)
- property management of administrative and business buildings
- Valuation of properties
- Capital markets (investment advices for selling building)

Industry/Entity Type

Real Estate

Colors

Designer to choose colors to be used in the design.

```html
<!DOCTYPE html>
<html lang="en">
<head>
<meta charset="utf-8">
<title>Luxembourg Office Market Report Q3-2013 – Meridane</title>
<link href="https://fonts.googleapis.com/css2?family=Arimo:wght@400;700&display=swap" rel="stylesheet">
<style>
  :root {
    --paper: #ffffff;
    --brand-orange: #f26522;
    --ink: #111111;
    --reverse: #ffffff;
    --photo-light: #d9d9d9;
    --photo-mid: #8a8a8a;
    --photo-dark: #2a2a2a;
  }
  * { margin: 0; padding: 0; box-sizing: border-box; }
  html, body {
    width: 873px;
    height: 1200px;
    overflow: hidden;
    background: var(--paper);
  }
  .cover {
    position: relative;
    width: 873px;
    height: 1200px;
    background: var(--paper);
    font-family: "Arimo", Arial, sans-serif;
  }
  .cover-photo {
    position: absolute;
    left: 28px;
    top: 25px;
    width: 815px;
    height: 620px;
    background:
      radial-gradient(ellipse at 30% 30%, var(--photo-light) 0%, transparent 45%),
      linear-gradient(135deg, var(--photo-mid) 0%, var(--photo-light) 35%, var(--photo-mid) 60%, var(--photo-dark) 100%);
  }
  .cover-band {
    position: absolute;
    left: 28px;
    top: 648px;
    width: 815px;
    height: 535px;
    background: var(--brand-orange);
    text-align: center;
  }
  .report-title {
    position: absolute;
    left: 0;
    right: 0;
    top: 102px;
    font-weight: 400;
    line-height: 1.4;
  }
  .report-title .place,
  .report-title .period {
    display: block;
    font-size: 38px;
    color: var(--ink);
  }
  .report-title .subject {
    display: block;
    font-size: 40px;
    font-weight: 700;
    color: var(--reverse);
  }
  .brand-name {
    position: absolute;
    left: 0;
    right: 0;
    top: 398px;
    font-size: 46px;
    font-weight: 700;
    letter-spacing: -1px;
    color: var(--reverse);
  }
</style>
</head>
<body>
  <main class="cover">
    <div class="cover-photo" role="img" aria-label="Black and white upward view of modern glass office towers against a cloudy sky"></div>
    <section class="cover-band">
      <h1 class="report-title">
        <span class="place">Luxembourg</span>
        <span class="subject">Office Market Report</span>
        <span class="period">Q3-2013</span>
      </h1>
      <div class="brand-name">MERIDANE</div>
    </section>
  </main>
</body>
</html>
```